Book Cover

Book cover for a study guide on Corvanians. The title would be: "Corvanians: Unbound to Walk Onward" Possibly using a bird breaking free from a cage.+

Target Market(s)

We will sell them to our church.

Requirements
Must have
• Authors are Dr. Martin Oskeby and Dr. Helena Oskeby

```html
<!DOCTYPE html>
<html lang="en">
<head>
<meta charset="utf-8">
<title>Corvanians: Unbound to Walk Onward — Book Cover</title>
<link href="https://fonts.googleapis.com/css2?family=Italiana&family=Montserrat:wght@400&family=Alegreya+Sans:wght@400&family=Crimson+Pro:wght@400&display=swap" rel="stylesheet">
<style>
  :root {
    --paper: #ffffff;
    --navy: #3c3f5a;
    --cream: #f4f1e1;
    --blossom: #d7a6d2;
    --leaf: #2f5a4e;
  }
  * { margin: 0; padding: 0; box-sizing: border-box; }
  html, body { width: 1200px; height: 735px; overflow: hidden; background: var(--paper); }
  .canvas { position: relative; width: 1200px; height: 735px; overflow: hidden; background: var(--paper); color: var(--cream); }
  .panel { position: absolute; top: 69px; height: 596px; background: var(--navy); overflow: hidden; }
  .back-cover { left: 82px; width: 453px; }
  .spine { left: 541px; width: 117px; }
  .front-cover { left: 665px; width: 453px; }

  .art { position: absolute; border-radius: 4px; }
  .art--cream { background: radial-gradient(ellipse at center, rgba(244,241,225,0.45), rgba(244,241,225,0.12)); }
  .art--flowers { background: radial-gradient(ellipse at 50% 70%, rgba(215,166,210,0.7), rgba(47,90,78,0.25) 70%, rgba(244,241,225,0.1)); }

  .title { position: absolute; font-family: "Italiana", serif; color: var(--cream); white-space: nowrap; text-align: center; letter-spacing: 0.02em; }
  .subtitle { position: absolute; font-family: "Montserrat", sans-serif; color: var(--cream); white-space: nowrap; text-align: center; letter-spacing: 0.03em; }

  .back-title { left: 249px; top: 135px; width: 180px; font-size: 29px; line-height: 32px; }
  .back-subtitle { left: 249px; top: 163px; width: 180px; font-size: 10px; line-height: 14px; }

  .bio-label { position: absolute; font-family: "Crimson Pro", serif; font-size: 12px; line-height: 14px; }
  .bio-name { position: absolute; left: 76px; font-family: "Alegreya Sans", sans-serif; font-size: 23px; line-height: 26px; white-space: nowrap; }
  .bio-text { position: absolute; left: 76px; width: 340px; font-family: "Crimson Pro", serif; font-size: 8.4px; line-height: 10px; }

  .spine-title, .spine-subtitle { transform: translate(-50%, -50%) rotate(90deg); }
  .spine-title { left: 71px; top: 300px; font-size: 47px; line-height: 48px; }
  .spine-subtitle { left: 40px; top: 300px; font-size: 15px; line-height: 18px; }

  .front-title { left: 0; width: 453px; top: 136px; font-size: 45px; line-height: 48px; }
  .front-subtitle { left: 0; width: 453px; top: 185px; font-size: 15px; line-height: 18px; letter-spacing: 0.04em; }

  .credits { position: absolute; left: 0; width: 453px; top: 494px; text-align: center; }
  .credits-label { font-family: "Crimson Pro", serif; font-size: 12px; line-height: 14px; }
  .credits-name { font-family: "Alegreya Sans", sans-serif; font-size: 23px; line-height: 21px; }
  .credits-amp { font-family: "Crimson Pro", serif; font-size: 20px; line-height: 18px; }

  .cross { position: absolute; left: 0; top: 0; width: 1200px; height: 735px; pointer-events: none; }
  .cross path { fill: none; stroke: var(--cream); stroke-width: 2.4; }
</style>
</head>
<body>
<div class="canvas">

  <section class="panel back-cover">
    <div class="art art--cream" style="left:30px; top:21px; width:201px; height:207px;" role="img" aria-label="Illustration of a bird flying out of an open hanging birdcage"></div>
    <div class="title back-title">CORVANIANS</div>
    <div class="subtitle back-subtitle">UNBOUND TO WALK ONWARD</div>

    <div class="bio-label" style="left:120px; top:281px;">Biografhy</div>
    <div class="bio-name" style="top:298px;">Dr. Martin Oskeby</div>
    <p class="bio-text" style="top:328px;">Book cover for a study guide on Corvanians. The title would be:<br>"Corvanians: Unbound to Walk Onward" Possibly using a bird breaking free from a cage.+<br>Book cover for a study guide on Corvanians. The title would be:<br>"Corvanians: Unbound to Walk Onward" Possibly using a bird breaking free from a cage.+</p>

    <div class="bio-label" style="left:139px; top:397px;">Biografhy</div>
    <div class="bio-name" style="top:414px;">Dr. Helena Oskeby</div>
    <p class="bio-text" style="top:444px;">Book cover for a study guide on Corvanians. The title would be:<br>"Corvanians: Unbound to Walk Onward" Possibly using a bird breaking free from a cage.+<br>Book cover for a study guide on Corvanians. The title would be:<br>"Corvanians: Unbound to Walk Onward" Possibly using a bird breaking free from a cage.+</p>
  </section>

  <section class="panel spine">
    <div class="art art--cream" style="left:14px; top:61px; width:95px; height:87px;" role="img" aria-label="Illustration of a bird in flight with motion lines"></div>
    <div class="title spine-title">CORVANIANS</div>
    <div class="subtitle spine-subtitle">UNBOUND TO WALK ONWARD</div>
    <div class="art art--cream" style="left:14px; top:451px; width:95px; height:86px;" role="img" aria-label="Illustration of a bird in flight with motion lines"></div>
  </section>

  <section class="panel front-cover">
    <div class="art art--cream" style="left:14px; top:136px; width:74px; height:76px;" role="img" aria-label="Small illustration of a bird leaving an open birdcage"></div>
    <div class="title front-title">CORVANIANS</div>
    <div class="subtitle front-subtitle">UNBOUND TO WALK ONWARD</div>
    <div class="art art--cream" style="left:370px; top:136px; width:75px; height:76px;" role="img" aria-label="Small illustration of a bird leaving an open birdcage"></div>
    <div class="art art--flowers" style="left:200px; top:341px; width:61px; height:135px;" role="img" aria-label="Illustration of pink blossoms with a leafy sprig"></div>
    <div class="credits">
      <div class="credits-label">Authors are :</div>
      <div class="credits-name">Dr. Martin Oskeby</div>
      <div class="credits-amp">&amp;</div>
      <div class="credits-name">Dr. Helena Oskeby</div>
    </div>
  </section>

  <svg class="cross" viewBox="0 0 1200 735" aria-hidden="true">
    <path d="M665 190 H840 V69"/>
    <path d="M852 69 V190 H934 V69"/>
    <path d="M946 69 V190 H1118"/>
    <path d="M712 199 H1072"/>
    <path d="M712 288 H1072"/>
    <path d="M665 297 H840 V568"/>
    <path d="M852 431 V297 H934 V431"/>
    <path d="M1118 297 H946 V568"/>
    <path d="M840 648 V665 M852 648 V665 M934 648 V665 M946 648 V665"/>
  </svg>

</div>
</body>
</html>
```